Need Help having my business card stand out

I am the owner of Birchway Canine Training and would like for my business cards to stand out. I have been trying to keep designing them myself but I can't get what I have in my head on the card. I will try my best to post templates that I like for inspirations. I want something unique but elegant. I don't want in to look cartoony or cheesy. It needs to pop in a pet shop but also in a coffee shop or gym.

Target Market(s)

Dog owners, Married ,No young kids Jr High school kids and up (maybe kids on the way) Executives, Stay at home moms/wives, Small business owners

Industry/Entity Type

Dog Training

Contact Information for Business Card

Lowell Spratt, 281-904-3376, info@birchwaycanine.example, www.birchwaycanine.example

Colors

Designer to choose colors to be used in the design.

Requirements
Must have
• my logo
Should not have
• Cursive lettering

```html
<!DOCTYPE html>
<html lang="en">
<head>
<meta charset="utf-8">
<title>Birchway Canine Training – Business Card</title>
<link href="https://fonts.googleapis.com/css2?family=Open+Sans:ital,wght@0,400;0,700;0,800;1,400&family=Josefin+Sans:wght@300&display=swap" rel="stylesheet">
<style>
  :root {
    --backdrop: #9a5f5f;
    --card: #7d3d46;
    --card-deep: #6a2d36;
    --band-light: #b87674;
    --band-dark: #7e3f44;
    --mark: #5a0b14;
    --text-light: #ffffff;
    --text-muted: #c98f8c;
  }
  * { margin: 0; padding: 0; box-sizing: border-box; }
  html, body { width: 1200px; height: 900px; overflow: hidden; }
  body {
    background: var(--backdrop);
    font-family: "Open Sans", Arial, sans-serif;
    position: relative;
  }
  .card {
    position: absolute;
    left: 250px;
    width: 700px;
    height: 400px;
    background: radial-gradient(circle at 40% 40%, var(--card) 0%, var(--card-deep) 100%);
    box-shadow: 0 10px 24px rgba(60, 20, 25, 0.45);
    overflow: hidden;
  }
  .card--front { top: 30px; }
  .card--back { top: 470px; }
  .card__shapes { position: absolute; inset: 0; width: 700px; height: 400px; }

  .brand-name {
    position: absolute;
    font-weight: 800;
    color: var(--mark);
    line-height: 1.05;
    text-align: center;
  }
  .card--front .brand-name { left: 360px; top: 130px; width: 290px; font-size: 40px; }
  .card--back .brand-name { left: 450px; top: 175px; width: 220px; font-size: 32px; }

  .contact-name {
    position: absolute; left: 80px; top: 78px;
    color: var(--text-light); font-size: 27px;
  }
  .contact-name strong { font-weight: 800; }
  .contact-role {
    position: absolute; left: 80px; top: 116px;
    font-family: "Josefin Sans", Arial, sans-serif; font-weight: 300;
    font-variant: small-caps; font-size: 20px; color: var(--text-muted);
  }
  .contact-list { position: absolute; left: 80px; top: 162px; list-style: none; }
  .contact-list li {
    display: flex; align-items: center; gap: 12px;
    height: 40px; color: var(--text-light);
    font-style: italic; font-size: 15px;
  }
  .contact-icon {
    width: 22px; height: 18px; background: var(--band-light);
    display: flex; align-items: center; justify-content: center;
  }
</style>
</head>
<body>

<section class="card card--front" aria-label="Card front">
  <svg class="card__shapes" viewBox="0 0 700 400">
    <defs>
      <linearGradient id="band-top" x1="0" y1="0" x2="1" y2="0">
        <stop offset="0" stop-color="#7e3f44"/>
        <stop offset="1" stop-color="#b87674"/>
      </linearGradient>
      <linearGradient id="band-bottom" x1="0" y1="0" x2="1" y2="0">
        <stop offset="0" stop-color="#b87674"/>
        <stop offset="1" stop-color="#7e3f44"/>
      </linearGradient>
    </defs>
    <polygon points="330,0 700,0 700,60" fill="url(#band-top)"/>
    <rect x="620" y="4" width="74" height="44" fill="#c4837f" opacity="0.35" role="img" aria-label="Paw print motif"/>
    <polygon points="0,290 520,400 0,400" fill="url(#band-bottom)"/>
    <rect x="8" y="300" width="50" height="76" fill="#c4837f" opacity="0.35" role="img" aria-label="Paw print motif"/>
    <rect x="160" y="0" width="60" height="170" rx="6" fill="#5a0b14"/>
    <circle cx="190" cy="136" r="24" fill="#d9a9a5"/>
  </svg>
  <div class="brand-name">Birchway Canine Training</div>
</section>

<section class="card card--back" aria-label="Card back">
  <svg class="card__shapes" viewBox="0 0 700 400">
    <defs>
      <linearGradient id="band-top-b" x1="0" y1="0" x2="1" y2="0">
        <stop offset="0" stop-color="#7e3f44"/>
        <stop offset="1" stop-color="#b87674"/>
      </linearGradient>
      <linearGradient id="band-bottom-b" x1="0" y1="0" x2="1" y2="0">
        <stop offset="0" stop-color="#b87674"/>
        <stop offset="1" stop-color="#7e3f44"/>
      </linearGradient>
    </defs>
    <polygon points="420,0 700,0 700,70" fill="url(#band-top-b)"/>
    <rect x="620" y="4" width="74" height="54" fill="#c4837f" opacity="0.35" role="img" aria-label="Paw print motif"/>
    <polygon points="0,300 520,400 0,400" fill="url(#band-bottom-b)"/>
    <rect x="8" y="310" width="50" height="80" fill="#c4837f" opacity="0.35" role="img" aria-label="Paw print motif"/>
  </svg>

  <h1 class="contact-name"><strong>Lowell</strong> Spratt</h1>
  <p class="contact-role">Designation</p>
  <ul class="contact-list">
    <li>
      <span class="contact-icon"><svg width="12" height="14" viewBox="0 0 12 14"><path d="M6 0a5 5 0 0 1 5 5c0 4-5 9-5 9S1 9 1 5a5 5 0 0 1 5-5z" fill="#5a0b14"/><circle cx="6" cy="5" r="2" fill="#b87674"/></svg></span>
      000 Alder Row, Suite 300, Fenwick, US 0000
    </li>
    <li>
      <span class="contact-icon"><svg width="14" height="12" viewBox="0 0 14 12"><path d="M1 4q6-5 12 0v2h-3V4H4v2H1z" fill="#5a0b14"/><rect x="3" y="6" width="8" height="5" fill="#5a0b14"/></svg></span>
      281-904-3376
    </li>
    <li>
      <span class="contact-icon"><svg width="14" height="10" viewBox="0 0 14 10"><rect x="0.5" y="0.5" width="13" height="9" fill="none" stroke="#5a0b14"/><path d="M0.5 0.5 7 6l6.5-5.5" fill="none" stroke="#5a0b14"/></svg></span>
      info@birchwaycanine.example
    </li>
    <li>
      <span class="contact-icon"><svg width="14" height="14" viewBox="0 0 14 14"><circle cx="7" cy="7" r="6" fill="none" stroke="#5a0b14"/><ellipse cx="7" cy="7" rx="2.5" ry="6" fill="none" stroke="#5a0b14"/><path d="M1 7h12" stroke="#5a0b14"/></svg></span>
      www.birchwaycanine.example
    </li>
  </ul>

  <div class="brand-name">Birchway Canine Training</div>
</section>

</body>
</html>
```